Harbor Crestline (Business Card Design)

Need business cards designed. Something modern, chic, and sleek. Mabye the back of the card should be the navy blue that is in the logo and then just the logo on the back.

Target Market(s)

Those in the hotel, office, and renovation industry

Contact Information for Business Card

1. Logo 2. Dorian Fenwick 3. CEO/Founder 4. Phone: (833) HarbCre / (833) 427-2731 5. Email: dorian@theharborcrestline.com 6. Website: www.theharborcrestline.com

Font styles to use
Other font styles liked:
• Look at the logo font and base the font for everything else off of that.

Colors
0054AA
0677BA
7BADD7
CADEEF
E8F1F8

Requirements
Must have
• Colors that are associated in the logo
Nice to have
• Sleek modern clean and chic design.

```html
<!DOCTYPE html>
<html lang="en">
<head>
<meta charset="UTF-8">
<title>Harbor Crestline — Business Card</title>
<link rel="stylesheet" href="https://fonts.googleapis.com/css2?family=Montserrat:wght@500&family=Poppins:wght@400;500;600&display=swap">
<style>
  :root {
    --page-bg: #ffffff;
    --navy-front: #0c1631;
    --navy-back: #0b1024;
    --white: #ffffff;
    --gold: #d6a737;
    --shadow: rgba(0, 0, 0, 0.35);
  }
  * { margin: 0; padding: 0; box-sizing: border-box; }
  html, body {
    width: 722px;
    height: 1200px;
    overflow: hidden;
    background: var(--page-bg);
  }
  .canvas {
    position: relative;
    width: 722px;
    height: 1200px;
  }
  .card {
    position: absolute;
    top: 337px;
    width: 300px;
    height: 525px;
    box-shadow: 8px 10px 18px var(--shadow);
    overflow: hidden;
  }
  .card-front {
    left: 41px;
    background: var(--navy-front);
  }
  .card-back {
    left: 381px;
    background: var(--navy-back);
  }
  .front-texture {
    position: absolute;
    inset: 0;
    background: linear-gradient(180deg, #0d1733 0%, #0b1530 100%);
  }
  .brand {
    position: absolute;
    left: 0;
    right: 0;
    top: 300px;
    text-align: center;
  }
  .brand-mark {
    display: block;
    width: 12px;
    height: 12px;
    margin: 0 auto 14px;
    background: var(--gold);
  }
  .brand-name {
    font-family: "Montserrat", sans-serif;
    font-weight: 500;
    font-size: 20px;
    letter-spacing: 2.5px;
    color: var(--white);
  }

  /* Large brand feature on the contact side */
  .back-feature {
    position: absolute;
    left: 16px;
    top: 52px;
    width: 260px;
  }
  .back-feature-mark {
    display: block;
    width: 18px;
    height: 18px;
    margin-bottom: 22px;
    background: var(--gold);
  }
  .back-feature-name {
    font-family: "Montserrat", sans-serif;
    font-weight: 500;
    font-size: 38px;
    line-height: 48px;
    letter-spacing: 3px;
    color: var(--white);
  }

  .person {
    position: absolute;
    left: 16px;
    top: 355px;
    font-family: "Poppins", sans-serif;
  }
  .person-name {
    font-weight: 600;
    font-size: 23px;
    line-height: 26px;
    color: var(--white);
    letter-spacing: 0.3px;
  }
  .person-name .surname { color: var(--gold); }
  .person-title {
    font-weight: 500;
    font-size: 14px;
    line-height: 18px;
    color: var(--gold);
  }
  .contact-list {
    list-style: none;
    position: absolute;
    left: 18px;
    top: 411px;
    font-family: "Poppins", sans-serif;
    font-weight: 400;
    font-size: 12.3px;
    line-height: 23.3px;
    color: var(--white);
  }
</style>
</head>
<body>
<main class="canvas">
  <section class="card card-front">
    <div class="front-texture" role="img" aria-label="Subtle tone-on-tone hexagon background pattern"></div>
    <div class="brand">
      <span class="brand-mark"></span>
      <div class="brand-name">HARBOR CRESTLINE</div>
    </div>
  </section>

  <section class="card card-back">
    <div class="back-feature">
      <span class="back-feature-mark"></span>
      <div class="back-feature-name">HARBOR<br>CRESTLINE</div>
    </div>
    <div class="person">
      <div class="person-name">DORIAN <span class="surname">FENWICK</span></div>
      <div class="person-title">CEO/Founder</div>
    </div>
    <ul class="contact-list">
      <li>(833) 427-2731</li>
      <li>(833) HarbCre</li>
      <li>dorian@theharborcrestline.com</li>
      <li>www.theharborcrestline.com</li>
    </ul>
  </section>
</main>
</body>
</html>
```